SkyvornQ Business Cards and Stationary Design

Need a design for our business cards and stationary. I want to carry on the theme of the logo. I want the business cards to have a design on the back. I would like the business cards and the stationary to carry the same theme, design scheme, and branding

Target Market(s)

Airlines and Maintenance Facilities

Industry/Entity Type

Aviation

Contact Information for Business Card

Name
Position Title
Address: 4827 Trellis Hollow Road, Fort Pierce, Florida, 34951
Office Number
Mobile Number
Email
Website

Font styles to use
Serif
Sans Serif

Colors

Designer to choose colors to be used in the design.

```html
<!DOCTYPE html>
<html lang="en">
<head>
<meta charset="utf-8">
<title>SkyvornQ Business Cards</title>
<link rel="stylesheet" href="https://fonts.googleapis.com/css2?family=Open+Sans:wght@400;600;700;800&display=swap">
<style>
  :root {
    --navy: #0e3470;
    --sky: #1ea0e6;
    --white: #ffffff;
    --stage: #e9e6e3;
    --ink: #14325f;
  }
  html, body {
    margin: 0;
    padding: 0;
    width: 1200px;
    height: 997px;
    overflow: hidden;
    background: var(--stage);
    font-family: "Open Sans", Arial, sans-serif;
  }
  .stage {
    width: 1200px;
    height: 997px;
    display: flex;
    align-items: center;
    justify-content: center;
    gap: 50px;
  }
  .card {
    position: relative;
    width: 540px;
    height: 310px;
    background: var(--white);
    box-shadow: 0 6px 18px rgba(0,0,0,0.12);
    overflow: hidden;
  }
  .card-art {
    position: absolute;
    inset: 0;
    width: 540px;
    height: 310px;
  }
  .contact {
    position: absolute;
    left: 28px;
    top: 52px;
    color: var(--white);
    font-size: 12px;
    line-height: 1.45;
  }
  .contact-name {
    font-weight: 700;
    font-size: 16px;
    letter-spacing: 0.5px;
    margin: 0;
  }
  .contact-title {
    margin: 0 0 12px;
    font-size: 12px;
    opacity: 0.9;
  }
  .contact-address {
    margin: 0 0 4px;
    width: 190px;
  }
  .contact-list {
    list-style: none;
    margin: 0;
    padding: 0;
  }
  .contact-list li {
    display: flex;
    align-items: center;
    gap: 6px;
    height: 19px;
  }
  .contact-icon {
    width: 13px;
    height: 13px;
    flex: none;
  }
  .brand {
    display: flex;
    flex-direction: column;
    align-items: center;
    color: var(--navy);
  }
  .brand-dot {
    border-radius: 50%;
    border: 5px solid var(--sky);
    box-sizing: border-box;
  }
  .brand-name {
    font-weight: 800;
    margin: 0;
    color: var(--navy);
    white-space: nowrap;
  }
  .card-front .brand {
    position: absolute;
    right: 26px;
    top: 118px;
    width: 160px;
  }
  .card-front .brand-dot { width: 46px; height: 46px; margin-bottom: 10px; }
  .card-front .brand-name { font-size: 21px; letter-spacing: 3px; }
  .card-back .brand {
    position: absolute;
    left: 0;
    right: 0;
    top: 62px;
  }
  .card-back .brand-dot { width: 66px; height: 66px; margin-bottom: 18px; }
  .card-back .brand-name { font-size: 36px; letter-spacing: 6px; }
  .web-line {
    display: flex;
    align-items: center;
    gap: 12px;
    margin-top: 12px;
    font-size: 13px;
    letter-spacing: 2px;
    color: var(--ink);
  }
  .web-line::before, .web-line::after {
    content: "";
    width: 70px;
    height: 1px;
    background: var(--navy);
  }
</style>
</head>
<body>
<main class="stage">

  <section class="card card-front" aria-label="Business card, contact side">
    <svg class="card-art" viewBox="0 0 540 310" aria-hidden="true">
      <path d="M0 0 H540 V10 C440 12 370 40 335 110 C300 190 250 250 0 268 Z" fill="var(--navy)"/>
      <path d="M0 268 C250 250 300 190 335 110 C322 200 262 272 0 288 Z" fill="var(--sky)"/>
      <path d="M372 112 C392 68 428 42 482 28 C440 50 408 78 384 114 Z" fill="var(--sky)"/>
    </svg>
    <div class="contact">
      <p class="contact-name">DORIAN PELL</p>
      <p class="contact-title">President</p>
      <p class="contact-address">4827 Trellis Hollow Road, Fort Pierce, Florida, 34951</p>
      <ul class="contact-list">
        <li>
          <svg class="contact-icon" viewBox="0 0 14 14"><circle cx="7" cy="7" r="7" fill="#fff"/><path d="M4.3 3.6 l1.3 0 l.6 1.8 -.8.7 a5 5 0 0 0 2.5 2.5 l.7-.8 1.8.6 0 1.3 c-3.5.3-6.4-2.6-6.1-6.1z" fill="var(--navy)"/></svg>
          <span>001 555 0148</span>
        </li>
        <li>
          <svg class="contact-icon" viewBox="0 0 14 14"><circle cx="7" cy="7" r="7" fill="#fff"/><rect x="5" y="3" width="4" height="8" rx="0.8" fill="var(--navy)"/><rect x="5.8" y="4" width="2.4" height="5" fill="#fff"/></svg>
          <span>001 555 0148</span>
        </li>
        <li>
          <svg class="contact-icon" viewBox="0 0 14 14"><circle cx="7" cy="7" r="7" fill="#fff"/><rect x="3.5" y="4.5" width="7" height="5" fill="var(--navy)"/><path d="M3.5 4.5 L7 7.5 L10.5 4.5" stroke="#fff" stroke-width="0.8" fill="none"/></svg>
          <span>info@skyvornq.com</span>
        </li>
        <li>
          <svg class="contact-icon" viewBox="0 0 14 14"><circle cx="7" cy="7" r="7" fill="#fff"/><circle cx="7" cy="7" r="3.8" fill="none" stroke="var(--navy)" stroke-width="0.9"/><path d="M3.2 7 H10.8 M7 3.2 C5 5 5 9 7 10.8 M7 3.2 C9 5 9 9 7 10.8" stroke="var(--navy)" stroke-width="0.8" fill="none"/></svg>
          <span>www.skyvornq.com</span>
        </li>
      </ul>
    </div>
    <div class="brand">
      <div class="brand-dot"></div>
      <p class="brand-name">SKYVORNQ</p>
    </div>
  </section>

  <section class="card card-back" aria-label="Business card, brand side">
    <div class="brand">
      <div class="brand-dot"></div>
      <p class="brand-name">SKYVORNQ</p>
      <div class="web-line">www.skyvornq.com</div>
    </div>
  </section>

</main>
</body>
</html>
```